PixelHarbor Rangers (Ledgerline Nova)
A website dedicated to crypto education. We are a new company focused on blockchain edutainment (education and interesting and entertaining content about the blockchain space). We want a fun, clean/minimalist and modern website that is made up of an education platform which could be a website in it’s own right. It will be the reference point for our users/community for all of our other blockchain based content in the PHR website ecosystem which will be covering; crypto news, digital asset investing (including a technical and fundamental analysis subscription service), blockchain business solutions and an NFT section that will cover creative art projects (art, music, gaming and more). To feature a logins and payment system which may need a shopping basket set up for tutorial/educational platform that is accessed via the website, NFT page with sub-categories: education and NFT and metaverse/virtual world and merchandise shopping page which is Web 3.0 enabled (able to link to a VeloPurse, Keelstone Vault etc , digital asset education page featuring blog and newsletter subscriptions links, A social media page where people can access videos, podcasts and our presence on other platforms such as Chirplo, Snapmora, Huddlex, Wirepost etc.
Number of Pages Required
5+ page
Look and feel

```html
<!DOCTYPE html>
<html lang="en">
<head>
<meta charset="utf-8">
<title>PixelHarbor Rangers</title>
<link href="https://fonts.googleapis.com/css2?family=Bree+Serif&family=Roboto:wght@400;500;700&display=swap" rel="stylesheet">
<style>
:root{
  --night:#0b0c20;
  --card:#14152f;
  --violet:#5b0fe6;
  --violet-btn:#5a12f0;
  --magenta:#8a12ee;
  --white:#ffffff;
  --soft:#d9d4f5;
  --green:#4bf02a;
  --pink:#d21cf0;
  --cyan:#1fb6f0;
}
*{margin:0;padding:0;box-sizing:border-box}
html,body{width:1200px;height:4258px;overflow:hidden;background:var(--night)}
body{font-family:'Roboto',sans-serif;color:var(--white);position:relative}
section,header,footer{position:absolute;left:0;width:1200px}
.abs{position:absolute}
.center{text-align:center;left:0;width:1200px}
.title{font-family:'Bree Serif',serif;font-weight:400;font-size:38px}
.rule{position:absolute;left:578px;width:44px;height:3px;background:var(--white)}
.lead{font-size:19px;color:var(--soft)}
.btn{position:absolute;background:var(--violet-btn);color:var(--white);font-family:'Bree Serif',serif;border-radius:30px;display:flex;align-items:center;justify-content:center}
.photo{position:absolute}
.sprite{position:absolute}

.hero{top:0;height:760px;background:radial-gradient(ellipse at 50% 40%,#2a2f6a 0%,#1a1c46 40%,#120f2c 75%,#2a1130 100%)}
.logo{left:110px;top:26px;font-family:'Bree Serif',serif;font-size:34px;line-height:40px;text-align:center}
.pill{position:absolute;top:22px;height:40px;border-radius:20px;background:var(--violet-btn);font-family:'Bree Serif',serif;font-size:14px;display:flex;align-items:center;justify-content:center}
.nav{position:absolute;top:90px;font-family:'Bree Serif',serif;font-size:13px;letter-spacing:.3px}
.hero h1{position:absolute;top:340px;font-family:'Bree Serif',serif;font-size:52px;font-weight:400;letter-spacing:1px}
.hero p{position:absolute;top:422px;font-family:'Bree Serif',serif;font-size:20px;line-height:37px}

.eco{top:760px;height:686px;background:var(--night)}
.eco-card{position:absolute;width:472px;height:204px;background:var(--card);border-radius:4px}
.eco-card .photo{left:10px;top:14px;width:186px;height:176px;border-radius:4px}
.eco-card h3{position:absolute;left:230px;font-family:'Bree Serif',serif;font-weight:400;font-size:19px;line-height:28px}
.eco-card .bar{position:absolute;left:230px;width:36px;height:2px;background:var(--violet-btn)}
.eco-card p{position:absolute;left:232px;width:220px;font-size:13px;line-height:25px;color:var(--soft)}

.nft{top:1446px;height:476px;background:var(--violet)}
.nft-item{position:absolute;top:158px;width:260px;text-align:center}
.ring{width:146px;height:146px;border:2px solid var(--white);border-radius:50%;margin:0 auto;display:flex;align-items:center;justify-content:center}
.nft-item h4{font-family:'Bree Serif',serif;font-weight:400;font-size:25px;margin-top:14px}
.nft-item p{font-size:13.5px;line-height:25px;margin-top:8px;color:var(--soft)}

.tutorial{top:1922px;height:652px;background:linear-gradient(180deg,#141a3a 0%,#0d1130 100%)}
.video{position:absolute;top:143px;width:468px;height:285px}
.play{position:absolute;left:192px;top:100px;width:84px;height:84px;border-radius:50%;border:2px solid var(--white);background:rgba(0,0,0,.35);display:flex;align-items:center;justify-content:center}
.chat{position:absolute;right:0;bottom:0;width:58px;height:48px;background:var(--violet-btn);border-radius:48px 0 0 0;display:flex;align-items:center;justify-content:center}
.cap{position:absolute;top:452px;font-family:'Bree Serif',serif;font-size:17px}
.mini{position:absolute;top:498px;display:flex;gap:7px}
.mini span{width:15px;height:15px;border-radius:3px;background:var(--white)}

.edu{top:2574px;height:534px;background:linear-gradient(90deg,#7e0fe8 0%,#8d16ee 60%,#7a10e6 100%)}
.post{position:absolute;top:176px;width:312px}
.post .photo{position:relative;width:312px;height:210px}
.post .date{margin-top:18px;font-size:16px}
.post p{margin-top:10px;font-family:'Bree Serif',serif;font-size:15px;line-height:25px}

.features{top:3108px;height:471px;background:var(--night)}
.feat{position:absolute;top:182px;width:210px;text-align:center}
.feat .ring{width:132px;height:132px}
.feat p{margin-top:22px;font-family:'Bree Serif',serif;font-size:19px;line-height:25px;color:#e6e3f7}

.news{top:3579px;height:360px;background:var(--violet)}
.field{position:absolute;left:210px;top:171px;width:780px;height:55px;border-radius:28px;background:var(--white);color:#555;font-size:14px;padding-left:28px;display:flex;align-items:center}
.submit{position:absolute;left:525px;top:253px;width:151px;height:57px;border:2px solid var(--white);border-radius:30px;font-family:'Bree Serif',serif;font-size:18px;display:flex;align-items:center;justify-content:center}

.foot{top:3939px;height:319px;background:var(--night)}
.wallet{position:absolute;left:146px;display:flex;align-items:center;gap:14px;font-family:'Roboto',sans-serif;font-weight:500}
.divider{position:absolute;top:72px;width:1px;height:120px;background:#3a3b5a}
.info-h{font-family:'Roboto',sans-serif;font-size:19px}
.info-t{font-size:13px;line-height:23px;color:#d0cfe2}
.soc{position:absolute;top:166px;display:flex;gap:14px}
.soc span{width:40px;height:40px;border:2px solid var(--white);border-radius:50%}
.cards{position:absolute;left:922px;top:4210px;display:flex;gap:3px}
.cards span{width:32px;height:22px;border-radius:3px;background:#e9e9f1}
</style>
</head>
<body>

<header class="hero">
  <div class="photo" role="img" aria-label="Dark blue digital particle field background" style="left:0;top:0;width:1200px;height:760px;background:radial-gradient(circle at 20% 70%,rgba(120,40,120,.35),transparent 40%),radial-gradient(circle at 80% 30%,rgba(70,90,180,.35),transparent 45%)"></div>
  <div class="abs logo">PixelHarbor<br>Rangers</div>
  <div class="pill" style="left:785px;width:122px">REGISTER</div>
  <div class="pill" style="left:915px;width:175px">USER COMMUNITY</div>
  <div class="nav" style="left:481px">HOME</div>
  <div class="nav" style="left:579px">ABOUT US</div>
  <div class="nav" style="left:705px">NFT</div>
  <div class="nav" style="left:788px">BLOG</div>
  <div class="nav" style="left:882px">GALLERY</div>
  <div class="nav" style="left:1000px">CONTACT US</div>
  <h1 class="center">PIXELHARBOR RANGERS</h1>
  <p class="center">Sed ut perspiciatis unde omnis iste natus error sit voluptatem sit<br>accusantium doloremque laudantium</p>
  <div class="btn" style="left:512px;top:512px;width:176px;height:56px;font-size:19px">Get Started</div>
</header>

<section class="eco">
  <div class="sprite" role="img" aria-label="Green pixel creature character" style="left:220px;top:-44px;width:108px;height:66px;background:var(--green)"></div>
  <div class="sprite" role="img" aria-label="Purple pixel invader character" style="left:968px;top:32px;width:108px;height:100px;background:#5b16e8"></div>
  <h2 class="title abs center" style="top:48px">PHR Ecosystem</h2>

  <div class="eco-card" style="left:110px;top:158px">
    <div class="photo" role="img" aria-label="Hands holding a phone with a crypto coin overlay" style="background:linear-gradient(135deg,#2a2e3c,#7a5a3a 55%,#1c1f2c)"></div>
    <h3 style="top:32px">Crypto News</h3><div class="bar" style="top:72px"></div>
    <p style="top:88px">Sed ut perspiciatis unde omnis iste natus error sit voluptatem accusant ium doloremque laudantium</p>
  </div>
  <div class="eco-card" style="left:617px;top:158px">
    <div class="photo" role="img" aria-label="Person typing on a laptop with a glowing network" style="background:linear-gradient(135deg,#0d2a3a,#1a5a6a 50%,#0a1420)"></div>
    <h3 style="top:32px">Digital Asset Investing</h3><div class="bar" style="top:72px"></div>
    <p style="top:88px">Sed ut perspiciatis unde omnis iste natus error sit voluptatem accusant ium doloremque laudantium</p>
  </div>
  <div class="eco-card" style="left:110px;top:402px">
    <div class="photo" role="img" aria-label="Glowing blockchain coin symbol on a dark background" style="background:linear-gradient(135deg,#06222c,#2a6a7a 45%,#8a5a2a 60%,#061820)"></div>
    <h3 style="top:16px">Blockchain Business<br>Solutions</h3><div class="bar" style="top:84px"></div>
    <p style="top:88px">Sed ut perspiciatis unde omnis iste natus error sit voluptatem accusant ium doloremque laudantium</p>
  </div>
  <div class="eco-card" style="left:617px;top:402px">
    <div class="photo" role="img" aria-label="Glowing blue cubes forming blocks" style="background:linear-gradient(135deg,#0a1a5a,#1a5ae0 45%,#20d0f0 60%,#050a2a)"></div>
    <h3 style="top:32px">NFT</h3><div class="bar" style="top:72px"></div>
    <p style="top:88px">Sed ut perspiciatis unde omnis iste natus error sit voluptatem accusant ium doloremque laudantium</p>
  </div>
</section>

<section class="nft">
  <div class="sprite" role="img" aria-label="Green pixel creature character" style="left:128px;top:42px;width:108px;height:66px;background:var(--green)"></div>
  <h2 class="title abs center" style="top:40px">NFT</h2>
  <div class="rule" style="top:102px"></div>

  <div class="nft-item" style="left:136px">
    <div class="ring"><svg width="68" height="68" viewBox="0 0 68 68" fill="none" stroke="#fff" stroke-width="2.5" stroke-linecap="round"><path d="M10 58 L44 24 L52 32 L18 66 Z"/><path d="M44 24 L54 14 L62 22 L52 32"/><path d="M14 10 L58 54"/><path d="M10 14 L14 10 L24 20 L20 24 Z"/></svg></div>
    <h4>Art</h4><p>Sed ut perspiciatis unde omnis iste<br>natus error sit voluptatem</p>
  </div>
  <div class="nft-item" style="left:473px">
    <div class="ring"><svg width="60" height="66" viewBox="0 0 60 66" fill="none" stroke="#fff" stroke-width="2.5"><path d="M20 52 V12 L52 4 V44"/><circle cx="13" cy="52" r="8"/><circle cx="45" cy="44" r="8"/></svg></div>
    <h4>Music</h4><p>Sed ut perspiciatis unde omnis iste<br>natus error sit voluptatem</p>
  </div>
  <div class="nft-item" style="left:811px">
    <div class="ring"><svg width="72" height="66" viewBox="0 0 72 66" fill="none" stroke="#fff" stroke-width="2.5" stroke-linecap="round"><path d="M36 4 V22"/><rect x="4" y="22" width="64" height="40" rx="12"/><path d="M18 36 V48 M12 42 H24"/><circle cx="50" cy="38" r="2"/><circle cx="56" cy="44" r="2"/></svg></div>
    <h4>Gaming</h4><p>Sed ut perspiciatis unde omnis iste<br>natus error sit voluptatem</p>
  </div>
</section>

<section class="tutorial">
  <div class="sprite" role="img" aria-label="Magenta pixel invader character" style="left:982px;top:18px;width:132px;height:112px;background:var(--pink)"></div>
  <h2 class="title abs center" style="top:40px;font-size:36px">PixelHarbor Tutorial</h2>
  <div class="rule" style="top:100px"></div>

  <div class="video" style="left:110px">
    <div class="photo" role="img" aria-label="Person working on a laptop in a blue-lit server room" style="left:0;top:0;width:468px;height:285px;background:linear-gradient(135deg,#0a2a5a,#1e5aa0 45%,#0a1630)"></div>
    <div class="play"><svg width="28" height="30" viewBox="0 0 28 30"><path d="M4 2 L26 15 L4 28 Z" fill="#fff"/></svg></div>
    <div class="chat"><svg width="22" height="20" viewBox="0 0 22 20" fill="none" stroke="#fff" stroke-width="1.8"><ellipse cx="11" cy="9" rx="9" ry="7"/><path d="M5 14 L3 19 L9 15"/></svg></div>
  </div>
  <div class="video" style="left:623px">
    <div class="photo" role="img" aria-label="Circuit board with a glowing padlock" style="left:0;top:0;width:467px;height:285px;background:linear-gradient(135deg,#0a1a2a,#2a3a4a 40%,#8a7a2a 55%,#0a1420)"></div>
    <div class="play"><svg width="28" height="30" viewBox="0 0 28 30"><path d="M4 2 L26 15 L4 28 Z" fill="#fff"/></svg></div>
    <div class="chat"><svg width="22" height="20" viewBox="0 0 22 20" fill="none" stroke="#fff" stroke-width="1.8"><ellipse cx="11" cy="9" rx="9" ry="7"/><path d="M5 14 L3 19 L9 15"/></svg></div>
  </div>
  <div class="cap" style="left:110px">Sed ut perspiciatis unde omnis</div>
  <div class="cap" style="left:537px;font-size:16px;top:454px">Free</div>
  <div class="cap" style="left:623px">Sed ut perspiciatis unde omnis</div>
  <div class="cap" style="left:1048px;font-size:16px;top:454px">Paid</div>
  <div class="mini" style="left:110px" aria-label="Chirplo, Snapmora, Huddlex, Wirepost"><span></span><span></span><span></span><span></span></div>
  <div class="mini" style="left:623px" aria-label="Chirplo, Snapmora, Huddlex, Wirepost"><span></span><span></span><span></span><span></span></div>
  <div class="btn" style="left:495px;top:549px;width:210px;height:57px;font-size:17px">Check Your Result</div>
  <div class="sprite" role="img" aria-label="Cyan pixel invader character" style="left:62px;top:594px;width:82px;height:78px;background:var(--cyan)"></div>
</section>

<section class="edu">
  <h2 class="title abs center" style="top:40px;font-size:36px">Digital Asset Education</h2>
  <div class="rule" style="top:98px"></div>
  <p class="lead abs center" style="top:120px">Sed ut perspiciatis unde omnis iste natus error sit voluptatem accusantium</p>
  <svg class="abs" style="left:54px;top:236px" width="18" height="72" viewBox="0 0 18 72" fill="none" stroke="#fff" stroke-width="2"><path d="M16 2 L2 36 L16 70"/></svg>
  <svg class="abs" style="left:1134px;top:236px" width="18" height="72" viewBox="0 0 18 72" fill="none" stroke="#fff" stroke-width="2"><path d="M2 2 L16 36 L2 70"/></svg>
  <div class="post" style="left:110px">
    <div class="photo" role="img" aria-label="Blue and purple circuit board chip" style="background:linear-gradient(135deg,#1a1a6a,#4a3ad0 50%,#1a1050)"></div>
    <div class="date">28 Feb 2022</div>
    <p>Sed ut perspiciatis unde omnis iste natus error sit voluptatem accusantium</p>
  </div>
  <div class="post" style="left:445px">
    <div class="photo" role="img" aria-label="Hand holding a glowing NFT sign" style="background:linear-gradient(135deg,#1a1a2a,#6a5a5a 50%,#2a2a3a)"></div>
    <div class="date">28 Feb 2022</div>
    <p>Sed ut perspiciatis unde omnis iste natus error sit voluptatem accusantium</p>
  </div>
  <div class="post" style="left:779px">
    <div class="photo" role="img" aria-label="Phone showing a neon NFT screen" style="background:linear-gradient(135deg,#0a1a1a,#1a5a3a 45%,#c8c040 55%,#0a0a1a)"></div>
    <div class="date">28 Feb 2022</div>
    <p>Sed ut perspiciatis unde omnis iste natus error sit voluptatem accusantium</p>
  </div>
  <div class="sprite" role="img" aria-label="Magenta pixel invader character" style="left:1050px;top:382px;width:132px;height:112px;background:#c020f0"></div>
</section>

<section class="features">
  <h2 class="title abs center" style="top:36px;font-size:36px">Our Features</h2>
  <div class="rule" style="top:94px"></div>
  <p class="lead abs center" style="top:115px">Sed ut perspiciatis unde omnis iste natus error sit voluptatem accusantium</p>

  <svg class="abs" style="left:310px;top:195px" width="86" height="30" viewBox="0 0 86 30" fill="none" stroke="#fff" stroke-width="1.6" stroke-dasharray="4 4"><path d="M2 22 Q40 0 80 20"/><path d="M74 12 L82 21 L72 24" stroke-dasharray="none"/></svg>
  <svg class="abs" style="left:560px;top:315px" width="86" height="30" viewBox="0 0 86 30" fill="none" stroke="#fff" stroke-width="1.6" stroke-dasharray="4 4"><path d="M2 8 Q40 30 80 10"/><path d="M72 6 L82 9 L76 18" stroke-dasharray="none"/></svg>
  <svg class="abs" style="left:812px;top:195px" width="86" height="30" viewBox="0 0 86 30" fill="none" stroke="#fff" stroke-width="1.6" stroke-dasharray="4 4"><path d="M2 22 Q40 0 80 20"/><path d="M74 12 L82 21 L72 24" stroke-dasharray="none"/></svg>

  <div class="feat" style="left:118px">
    <div class="ring"><svg width="60" height="50" viewBox="0 0 60 50" fill="none" stroke="#fff" stroke-width="2"><ellipse cx="30" cy="20" rx="26" ry="14"/><path d="M4 20 V30 C4 38 16 44 30 44 C44 44 56 38 56 30 V20"/><circle cx="24" cy="20" r="6"/><circle cx="36" cy="20" r="6"/></svg></div>
    <p>Earn Tokens</p>
  </div>
  <div class="feat" style="left:371px">
    <div class="ring"><svg width="54" height="64" viewBox="0 0 54 64" fill="none" stroke="#fff" stroke-width="2"><circle cx="20" cy="16" r="5"/><path d="M14 26 H26 L28 44 H12 Z"/><path d="M16 44 V60 M24 44 V60"/><path d="M34 60 V4 L48 9 L34 14"/><path d="M8 60 H48"/></svg></div>
    <p>Achieving Levels</p>
  </div>
  <div class="feat" style="left:623px">
    <div class="ring"><svg width="66" height="62" viewBox="0 0 66 62" fill="none" stroke="#fff" stroke-width="2"><circle cx="33" cy="8" r="5"/><circle cx="8" cy="22" r="5"/><circle cx="58" cy="22" r="5"/><circle cx="12" cy="50" r="5"/><circle cx="54" cy="50" r="5"/><circle cx="33" cy="30" r="9"/><path d="M33 13 V21 M13 24 L25 28 M53 24 L41 28 M16 46 L26 36 M50 46 L40 36"/><path d="M22 58 Q33 48 44 58"/></svg></div>
    <p>Contributing to<br>the Community<br>Ecosystem</p>
  </div>
  <div class="feat" style="left:875px">
    <div class="ring"><svg width="66" height="60" viewBox="0 0 66 60" fill="none" stroke="#fff" stroke-width="2"><path d="M4 24 H14 L30 14 V44 L14 34 H4 Z"/><path d="M8 34 L12 48 H18 L16 36"/><rect x="36" y="6" width="24" height="18" rx="3"/><rect x="38" y="30" width="24" height="14" rx="3"/><circle cx="42" cy="52" r="5"/><path d="M40 12 H56 M40 18 H52 M42 36 H58"/></svg></div>
    <p>Marketing via<br>Social Media</p>
  </div>
</section>

<section class="news">
  <h2 class="title abs center" style="top:46px;font-size:36px">Newsletter Subscriptions</h2>
  <div class="rule" style="top:104px"></div>
  <p class="lead abs center" style="top:126px;font-size:18px">Sed ut perspiciatis unde omnis iste natus error sit voluptatem accusantium doloremque</p>
  <div class="field">Enter Your Email id :</div>
  <div class="submit">SUBMIT</div>
</section>

<footer class="foot">
  <div class="wallet" style="top:68px;font-size:24px;letter-spacing:5px"><span style="width:40px;height:40px;border-radius:6px;background:#e8822a"></span>VELOPURSE</div>
  <div class="wallet" style="top:134px;font-size:26px"><span style="width:54px;height:54px;border-radius:12px;background:var(--white)"></span>Keelstone Vault</div>
  <div class="divider" style="left:442px"></div>
  <div class="divider" style="left:772px"></div>

  <svg class="abs" style="left:464px;top:74px" width="18" height="24" viewBox="0 0 18 24" fill="none" stroke="#fff" stroke-width="1.6"><path d="M9 22 C9 22 2 13 2 8 A7 7 0 0 1 16 8 C16 13 9 22 9 22 Z"/><circle cx="9" cy="8" r="2.5"/></svg>
  <div class="abs" style="left:503px;top:70px"><div class="info-h">ADDRESS</div><div class="info-t"># 254 Lorem Ipsum Dummy<br>Lorem Ipsum Dummy</div></div>
  <div class="soc" style="left:503px" aria-label="Chirplo, Snapmora, Huddlex, Wirepost"><span></span><span></span><span></span><span></span></div>

  <svg class="abs" style="left:808px;top:76px" width="20" height="20" viewBox="0 0 20 20" fill="none" stroke="#fff" stroke-width="1.5"><path d="M3 2 L7 2 L9 7 L6 9 C7 12 9 14 11 15 L13 12 L18 14 L18 18 C10 19 2 11 3 2 Z"/></svg>
  <div class="abs" style="left:847px;top:70px"><div class="info-h">PHONE</div><div class="info-t">+1 888 888 8888</div></div>
  <svg class="abs" style="left:808px;top:148px" width="22" height="16" viewBox="0 0 22 16" fill="none" stroke="#fff" stroke-width="1.5"><rect x="1" y="1" width="20" height="14"/><path d="M1 1 L11 9 L21 1"/></svg>
  <div class="abs" style="left:849px;top:142px"><div class="info-h">EMAIL</div><div class="info-t">info@pixelharborrangers.example</div></div>

  <div class="abs" style="left:414px;top:271px;font-size:16px">© 2022 PixelHarbor Rangers.All rights reserved.</div>
</footer>
<div class="cards" aria-label="Accepted payment cards"><span></span><span></span><span></span><span></span><span></span></div>

</body>
</html>
```